Bold, Modern, Clean "Kestrelwaymassage.com" website

Why we stand out?
We are a male and female mobile massage team. Our names are Paul and Lina. 
Kestrel Way is a Seattle based mobile massage service. Our massage is offered to the community with a goal of facilitating balance within each individual. We specialize in integrated Pain management, and sports/medical massage therapy. Every client's first assessment is attended by our male and female massage therapist team. Depending on the goals identified for an individual determines which therapist will be assigned to provide treatment, if not both.

Our passion...
Here at Kestrel Way, we have a great passion for Postural Resoration and how it is integrated into an individual's Massage treatment. We pride ourselves in being natural facilitators of healing, which takes the ego of the therapist out of the client's healing process. We strive to deliver the best massage possible by including modalities such as Neuromuscular, Myofascial release, spontaneous muscle release, postural restoration, orthopedic, and medical massage.

Our education...

We are both Graduates of Venmora, school of massage therapy. We have continuing education in medical massage, myofacial release, trigger point therapy, postural restoration, anatomy, and spontaneous muscle release. Lina is also a Certified Yoga Instructor, which amplifies her experience with flexibility and strength as it pertains to each individual. Paul's passion is Massage, stretching, and strength training to encourage postural restoration and realignment.

Our rates-

Our rates are $75/ 60 minutes, $95/ 90 minutes, and $120/ 120 minutes.

Education-
Both Lina and I worked as behavioral health professionals that specialized in life skills mentoring for youth who had experienced different types of trauma. This led us both to want to help others in a different environment, where individuals can be empowered to take responsibility over their own healing. To us, massage is a type of manipulation physical therapy, that encourages healing on many levels.

Advice to any massage client-
The most important thing to 'us', as Licenced providers is to get you on to our table to show you our skills. But a good therapist never forgets that it's not about what we do for you, but what we can facilitate for you. Your health and healing has nothing to do with us. It is yours, not ours. Identify what your goals are with any Therapist, and know what the end looks like. Progress should be tangible, such as range of motion, and decreased pain.

Lina and Paul at Kestrel Way are awesome! I recently had open heart surgery, and Lina worked on me to increase my range of motion while helping with the pinched nerve from my arm being in the same position for so long during my surgery. My wife drives a lot for work, and Paul has helped decrease her neck and lower back pain immensely. They are seriously the best therapists I have ever worked with. I would recommend them to anyone who needs anything from stress relief to a medical massage treatment. They are professional, up beat, easy going, and always on time. And, I love that they meet us where ever we like! We did a staycation recently, where they came to our hotel to give us relaxation massages. Although usually they come to our home, where we focus on pain related issues. We will continue to work with them for a long, long time.

Target Market(s)

Mobile massage therapy clients

Industry/Entity Type

Massage Therapy

Coding

Coded - Design and coding required

Number of Pages Required

1 page

Font styles to use
Serif
Sans Serif

Requirements
Must have
• Please add or remove any information that would help the presentation of our website. Our logo is posted below, please include into the website.
• Please include a contact field that includes, kestrelwaymassage@fernmail.net,
• (206) 555-0148
• We have also included our own stock photos, as well as a photo of Paul and Lina. Please include a cropped photo of both massage therapists.

```html
<!DOCTYPE html>
<html lang="en">
<head>
<meta charset="utf-8">
<title>Kestrel Way – Mobile Massage</title>
<link rel="stylesheet" href="https://fonts.googleapis.com/css2?family=Raleway:wght@400;500;600;700&family=Roboto+Slab:wght@400;700&display=swap">
<style>
:root{
  --navy:#243a7c;
  --navy-deep:#1f3370;
  --cyan:#12b6e4;
  --white:#ffffff;
  --text:#555a66;
  --heading:#2b2f3a;
  --field:#dfe2ec;
  --hero-left:#3e5aa6;
  --photo-sky:#9fc6e0;
  --photo-skin:#e9c3b2;
}
*{box-sizing:border-box;margin:0;padding:0}
html,body{width:1200px;height:2239px;overflow:hidden;background:var(--white)}
body{position:relative;font-family:"Raleway",Arial,sans-serif;color:var(--text)}
.abs{position:absolute}
.slab{font-family:"Roboto Slab",Georgia,serif}

/* header */
.top-bar{left:0;top:0;width:1200px;height:48px;background:var(--navy)}
.top-phone{right:95px;top:13px;color:var(--white);font-size:15px;font-weight:600;display:flex;align-items:center;gap:12px}
.top-phone svg{width:26px;height:26px}
.nav-bar{left:0;top:48px;width:1200px;height:80px;background:var(--white)}
.brand{left:101px;top:16px;width:138px;height:138px;border-radius:50%;background:var(--navy);border:4px solid var(--white);box-shadow:0 0 0 3px var(--navy);display:flex;align-items:center;justify-content:center;text-align:center;color:var(--white);font-weight:700;font-size:25px;line-height:1;z-index:3}
.nav{top:72px;left:0;width:1200px;height:37px;font-size:15px;color:var(--heading);font-weight:500}
.nav a{position:absolute;top:0;height:37px;line-height:37px;color:inherit;text-decoration:none}
.nav a.active{background:var(--cyan);color:var(--white);border-radius:19px;padding:0 16px}

/* hero */
.hero-left{left:0;top:128px;width:600px;height:529px;background:linear-gradient(160deg,#4a64ad,var(--hero-left) 55%,#33509c)}
.hero-right{left:600px;top:128px;width:600px;height:529px;background:linear-gradient(180deg,var(--photo-sky) 0%,#c9dbe8 45%,var(--photo-skin) 100%)}
.hero-hello{left:0;width:600px;top:260px;text-align:center;color:var(--white);font-size:22px}
.hero-title{left:0;width:600px;top:310px;text-align:center;color:var(--white);font-size:42px;font-weight:700;letter-spacing:.5px}
.hero-copy{left:40px;width:520px;top:378px;text-align:center;color:var(--white);font-size:13px;line-height:20px}
.field{height:36px;background:var(--field);color:var(--heading);font-size:14px;padding-left:10px;line-height:36px}
.submit{height:36px;background:var(--cyan);color:var(--white);font-size:14px;font-weight:600;text-align:center;line-height:36px}
.dot{width:7px;height:7px;border-radius:50%;background:var(--white);top:595px}
.dot.on{background:var(--cyan)}
.hero-shadow{left:20px;top:657px;width:1160px;height:30px;background:radial-gradient(ellipse at top,rgba(0,0,0,.22),rgba(0,0,0,0) 70%)}

/* services */
.section-title{left:0;width:1200px;text-align:center;font-size:34px;color:var(--heading);display:flex;justify-content:center;align-items:center;gap:22px}
.section-title b{color:var(--navy);font-weight:700}
.leaf{width:30px;height:26px}
.section-sub{left:0;width:1200px;top:769px;text-align:center;font-size:14px}
.service{width:360px;text-align:center}
.service-ring{width:226px;height:226px;border-radius:50%;background:var(--navy);margin:0 auto;padding:14px}
.service-photo{width:198px;height:198px;border-radius:50%}
.service h3{font-size:23px;font-weight:500;color:var(--heading);margin-top:20px}
.service p{font-size:12.5px;line-height:19px;margin:8px auto 0;width:260px}

/* treatments band */
.treatments{left:0;top:1206px;width:1200px;height:424px;background:var(--navy)}
.treat-photo{width:181px;height:134px;border:3px solid var(--white)}
.treat-name{color:var(--white);font-size:17px;font-weight:600}
.price{width:40px;height:40px;border-radius:50%;background:var(--cyan);color:var(--white);font-size:15px;font-weight:600;text-align:center;line-height:40px}
.treat-list{list-style:none;color:var(--white);font-size:12.5px}
.treat-list li{height:34.5px;position:relative;padding-left:22px}
.treat-list li::before{content:"";position:absolute;left:2px;top:3px;width:6px;height:6px;border-right:2px solid var(--white);border-bottom:2px solid var(--white);transform:rotate(-45deg)}

/* education */
.edu-title{left:98px;top:1656px;font-size:27px;color:var(--heading);display:flex;align-items:center;gap:14px}
.edu-title b{color:var(--navy)}
.edu-copy{left:98px;top:1710px;width:657px;font-size:14px;line-height:22.3px;text-align:justify}
.read-more{left:600px;width:155px;top:1817px;text-align:right;font-size:14px;color:var(--navy);font-weight:500}
.rate{left:858px;width:240px;height:48px;border-radius:12px;background:var(--navy);color:var(--white);font-size:16px;font-weight:700;text-align:center;line-height:48px}
.rate.alt{background:var(--cyan)}

/* testimonial */
.quote-band{left:0;top:1895px;width:1200px;height:83px;background:var(--cyan)}
.quote-mark-icon{left:98px;top:1920px;width:38px;height:34px}
.quote-text{left:200px;top:1917px;width:730px;color:var(--white);font-size:13px;line-height:20px}
.quote-sign{color:var(--white);font-size:26px;font-family:Georgia,serif;font-weight:700}
.arrow-btn{width:30px;height:30px;border-radius:50%;border:1.5px solid var(--white);top:1921px}

/* footer */
.foot-brand{left:99px;top:2003px;width:92px;height:92px;border-radius:50%;background:var(--navy);border:3px solid var(--white);box-shadow:0 0 0 2px var(--navy);display:flex;align-items:center;justify-content:center;text-align:center;color:var(--white);font-weight:700;font-size:17px;line-height:1}
.foot-about{left:98px;top:2106px;width:220px;font-size:13px;line-height:19.5px;color:var(--heading)}
.divider{width:1px;top:2000px;height:150px;background:#dcdfe6}
.foot-col svg{width:26px;height:30px}
.foot-col h4{font-size:18px;font-weight:600;color:var(--heading);margin-top:12px}
.foot-col p{font-size:12.5px;line-height:19.5px;color:var(--heading);margin-top:8px}
.bottom-bar{left:0;top:2179px;width:1200px;height:60px;background:var(--navy)}
.copyright{left:98px;top:2197px;color:var(--white);font-size:15px}
.social{width:36px;height:36px;border-radius:50%;border:1.5px solid var(--white);top:2188px}
</style>
</head>
<body>

<header>
  <div class="abs top-bar"></div>
  <div class="abs top-phone">
    <svg viewBox="0 0 26 26" aria-hidden="true"><circle cx="13" cy="13" r="12" fill="none" stroke="#fff" stroke-width="1.5"/><path d="M9.2 7.5l2 2.6-1.2 1.5c.8 1.8 2.2 3.2 4 4l1.5-1.2 2.6 2-1.2 2c-4.6-.3-8.6-4.3-8.9-8.9z" fill="#fff"/></svg>
    (206) 555-0148
  </div>
  <div class="abs nav-bar"></div>
  <div class="abs brand">KESTREL<br>WAY</div>
  <nav class="abs nav">
    <a class="active" style="left:458px">Home</a>
    <a style="left:555px">Our Passion</a>
    <a style="left:681px">Our Education</a>
    <a style="left:822px">Our Rates</a>
    <a style="left:934px">Advice</a>
    <a style="left:1025px">Contact Us</a>
  </nav>
</header>

<section class="hero">
  <div class="abs hero-left" role="img" aria-label="Therapist's hands massaging a client, tinted blue"></div>
  <div class="abs hero-right" role="img" aria-label="Woman relaxing during a massage by the water"></div>
  <p class="abs hero-hello slab">Hello, We are Mobile Massage!!</p>
  <h1 class="abs hero-title slab">KESTREL WAY</h1>
  <p class="abs hero-copy">Claritas est etiam processus dynamicus, qui sequitur mutationem consuetudium lectorum. Mirum est notare quam littera gothica, quam nunc putamus</p>
  <div class="abs field" style="left:98px;top:451px;width:190px">Name</div>
  <div class="abs field" style="left:312px;top:451px;width:190px">Email</div>
  <div class="abs field" style="left:98px;top:510px;width:190px">Phone Number</div>
  <div class="abs submit" style="left:312px;top:510px;width:190px">SUBMIT NOW</div>
  <span class="abs dot" style="left:271px"></span>
  <span class="abs dot" style="left:296px"></span>
  <span class="abs dot on" style="left:321px"></span>
  <div class="abs hero-shadow"></div>
</section>

<section class="services">
  <h2 class="abs section-title slab" style="top:716px">
    <svg class="leaf" viewBox="0 0 30 26" aria-hidden="true"><path d="M2 24C4 10 14 3 28 2c-2 12-10 20-24 21 6-5 11-10 14-16C13 12 7 18 2 24z" fill="#12b6e4"/></svg>
    <span><b>Massage</b> Services</span>
    <svg class="leaf" viewBox="0 0 30 26" aria-hidden="true" style="transform:scaleX(-1)"><path d="M2 24C4 10 14 3 28 2c-2 12-10 20-24 21 6-5 11-10 14-16C13 12 7 18 2 24z" fill="#12b6e4"/></svg>
  </h2>
  <p class="abs section-sub">Neque porro quisquam est, qui dolorem ipsum quia dolor sit amet, consectetur, adipisci velit sedquia</p>

  <article class="abs service" style="left:60px;top:842px">
    <div class="service-ring"><div class="service-photo" role="img" aria-label="Therapist massaging a client's back" style="background:linear-gradient(135deg,#e7c9b5,#b9825f)"></div></div>
    <h3>Pain Management</h3>
    <p>Nemo enim ipsam voluptatem quia vo luptas sit aspernatur aut odit aut fugit, sed quia consequuntur magni dolores</p>
  </article>
  <article class="abs service" style="left:420px;top:842px">
    <div class="service-ring"><div class="service-photo" role="img" aria-label="Athlete receiving a leg stretch" style="background:linear-gradient(135deg,#f1ede8,#c79a80)"></div></div>
    <h3>Sports Massage</h3>
    <p>Nemo enim ipsam voluptatem quia vo luptas sit aspernatur aut odit aut fugit, sed quia consequuntur magni dolores</p>
  </article>
  <article class="abs service" style="left:786px;top:842px">
    <div class="service-ring"><div class="service-photo" role="img" aria-label="Seated shoulder massage on a massage chair" style="background:linear-gradient(135deg,#a9c7b7,#e4d5cd)"></div></div>
    <h3>Pain Management</h3>
    <p>Nemo enim ipsam voluptatem quia vo luptas sit aspernatur aut odit aut fugit, sed quia consequuntur magni dolores</p>
  </article>
</section>

<section class="abs treatments"></section>
<div class="abs treat-photo" style="left:98px;top:1269px;background:linear-gradient(135deg,#f1eeec,#d9b8a4)" role="img" aria-label="Hands working on a foot and calf"></div>
<h3 class="abs treat-name" style="left:307px;top:1268px">Neuromuscular</h3>
<div class="abs price" style="left:520px;top:1258px">$50</div>
<ul class="abs treat-list" style="left:307px;top:1311px"><li>Lorem ipsum dolor sit amet, consectetur</li><li>Adipiscing eliteger gravida velit quis dolo</li><li>Pellentesque elit tortor</li></ul>

<div class="abs treat-photo" style="left:639px;top:1269px;background:linear-gradient(135deg,#e8e2de,#c78f73)" role="img" aria-label="Cupping therapy on a client's back"></div>
<h3 class="abs treat-name" style="left:848px;top:1268px">Muscle Release</h3>
<div class="abs price" style="left:1059px;top:1258px">$50</div>
<ul class="abs treat-list" style="left:848px;top:1311px"><li>Lorem ipsum dolor sit amet, consectetur</li><li>Adipiscing eliteger gravida velit quis dolo</li><li>Pellentesque elit tortor</li></ul>

<div class="abs treat-photo" style="left:98px;top:1448px;background:linear-gradient(135deg,#eae4df,#c99478)" role="img" aria-label="Hands releasing tissue on an arm"></div>
<h3 class="abs treat-name" style="left:307px;top:1447px">Myofascial Release</h3>
<div class="abs price" style="left:520px;top:1437px">$50</div>
<ul class="abs treat-list" style="left:307px;top:1490px"><li>Lorem ipsum dolor sit amet, consectetur</li><li>Adipiscing eliteger gravida velit quis dolo</li><li>Pellentesque elit tortor</li></ul>

<div class="abs treat-photo" style="left:639px;top:1448px;background:linear-gradient(135deg,#3d3d3d,#8a8585)" role="img" aria-label="Person in a yoga backbend pose"></div>
<h3 class="abs treat-name" style="left:848px;top:1447px">Postural Restoration</h3>
<div class="abs price" style="left:1059px;top:1437px">$50</div>
<ul class="abs treat-list" style="left:848px;top:1490px"><li>Lorem ipsum dolor sit amet, consectetur</li><li>Adipiscing eliteger gravida velit quis dolo</li><li>Pellentesque elit tortor</li></ul>

<section class="education">
  <h2 class="abs edu-title slab">
    <svg class="leaf" viewBox="0 0 30 26" aria-hidden="true"><path d="M2 24C4 10 14 3 28 2c-2 12-10 20-24 21 6-5 11-10 14-16C13 12 7 18 2 24z" fill="#12b6e4"/></svg>
    <span>Our <b>Education</b></span>
  </h2>
  <p class="abs edu-copy">We are both Graduates of Venmora, school of massage therapy. We have con tinuing education in medical massage, myofacial release, trigger point therapy, postural restoration, anatomy, and spontaneous muscle release. Lina is also a Certified Yoga Instructor, which amplifies her experience with flexibility and strength as it pertains to each individual. Paul's passion is Massage, stretching, and strength training to encourage postural restoration and realignment.</p>
  <p class="abs read-more">- Read More</p>
  <div class="abs rate" style="top:1667px">$75/ 60 minutes</div>
  <div class="abs rate alt" style="top:1727px">$95/ 90 minutes</div>
  <div class="abs rate" style="top:1787px">$120/ 120 minutes</div>
</section>

<section class="testimonial">
  <div class="abs quote-band"></div>
  <svg class="abs quote-mark-icon" viewBox="0 0 38 34" aria-hidden="true"><circle cx="19" cy="17" r="15" fill="none" stroke="#fff" stroke-width="2"/></svg>
  <span class="abs quote-sign" style="left:175px;top:1908px">&ldquo;</span>
  <p class="abs quote-text">Nemo enim ipsam voluptatem quia voluptas sit aspernatur aut odit aut fugit, sed quia consequuntur magni dolores eos qui ratione voluptatem sequi nesciunt.</p>
  <span class="abs quote-sign" style="left:918px;top:1935px">&rdquo;</span>
  <svg class="abs arrow-btn" style="left:1028px" viewBox="0 0 30 30" aria-label="Previous"><path d="M17 9l-6 6 6 6" fill="none" stroke="#fff" stroke-width="2"/></svg>
  <svg class="abs arrow-btn" style="left:1072px" viewBox="0 0 30 30" aria-label="Next"><path d="M13 9l6 6-6 6" fill="none" stroke="#fff" stroke-width="2"/></svg>
</section>

<footer>
  <div class="abs foot-brand">KESTREL<br>WAY</div>
  <p class="abs foot-about">Neque porro quisquam est, qui do lorem ipsum quia dolor sit amet,</p>
  <div class="abs divider" style="left:354px"></div>
  <div class="abs divider" style="left:601px"></div>
  <div class="abs divider" style="left:894px"></div>

  <div class="abs foot-col" style="left:403px;top:2007px">
    <svg viewBox="0 0 26 30" aria-hidden="true"><path d="M13 28S3 17 3 11a10 10 0 0120 0c0 6-10 17-10 17z" fill="none" stroke="#12b6e4" stroke-width="2"/><circle cx="13" cy="11" r="3.5" fill="none" stroke="#12b6e4" stroke-width="2"/></svg>
    <h4>Visit Us</h4>
    <p>418 Harbor Lane<br>WESTFALL WA 98107<br>USA</p>
  </div>
  <div class="abs foot-col" style="left:669px;top:2007px">
    <svg viewBox="0 0 26 30" aria-hidden="true"><circle cx="13" cy="15" r="11" fill="none" stroke="#12b6e4" stroke-width="2"/><path d="M13 9v6l4 3" fill="none" stroke="#12b6e4" stroke-width="2"/></svg>
    <h4>Make happy with us</h4>
    <p>MON - FRI:10:00 - 16:00<br>SAT: 10:00 - 14:00<br>SUN: Closed</p>
  </div>
  <div class="abs foot-col" style="left:964px;top:2007px">
    <svg viewBox="0 0 36 30" aria-hidden="true" style="width:36px"><circle cx="9" cy="15" r="6" fill="none" stroke="#12b6e4" stroke-width="2"/><circle cx="27" cy="15" r="6" fill="none" stroke="#12b6e4" stroke-width="2"/><path d="M9 21h18" stroke="#12b6e4" stroke-width="2"/></svg>
    <h4>Talk to us</h4>
    <p>1900-1577-0148<br>+012 555 0193<br>hello@kestrelway.net</p>
  </div>

  <div class="abs bottom-bar"></div>
  <p class="abs copyright">Copyright © 2015 - Kestrel Way</p>
  <span class="abs social" style="left:957px" aria-label="Social link"></span>
  <span class="abs social" style="left:1010px" aria-label="Social link"></span>
  <span class="abs social" style="left:1064px" aria-label="Social link"></span>
</footer>

</body>
</html>
```